Heritage Hollow Business Cards

Require a business card design. <br/><br/>Needs to include logo (either round or long version) plus these details:<br/>Maya Torvell<br/>Heritage Hollow<br/>maya@kelvadtrading.com.au<br/>02 6481 7395<br/>PO Box Glenwarra NSW 2791<br/>www.heritagehollow.com.au<br/><br/>I need in an editable format so that I can create for multiple staff members. <br/><br/>

Target Market(s)

We are an online store selling renovation products to home owners are builders. Looking for a classic classy design.

Industry/Entity Type

Home And Garden

Contact Information for Business Card

Maya Torvell
Heritage Hollow
maya@kelvadtrading.com.au
02 6481 7395
PO Box Glenwarra NSW 2791
www.heritagehollow.com.au

Colors

Designer to choose colors to be used in the design.

Requirements
Must have
• Must include Logo.

```html
<!DOCTYPE html>
<html lang="en">
<head>
<meta charset="utf-8">
<title>Heritage Hollow Business Cards</title>
<link rel="stylesheet" href="https://fonts.googleapis.com/css2?family=Arimo:wght@400;700&display=swap">
<style>
  :root {
    --backdrop: #e9e4dc;
    --kraft-light: #dcbc8e;
    --kraft-mid: #c9a472;
    --kraft-dark: #b48a57;
    --ink: #1f1a15;
    --rule: #6b5539;
  }
  html, body {
    margin: 0;
    padding: 0;
    width: 1200px;
    height: 900px;
    overflow: hidden;
    background: var(--backdrop);
  }
  .canvas {
    position: relative;
    width: 1200px;
    height: 900px;
    font-family: "Arimo", Arial, sans-serif;
    color: var(--ink);
  }
  .card {
    position: absolute;
    left: 330px;
    width: 556px;
    height: 343px;
    background: radial-gradient(ellipse at 45% 10%, var(--kraft-light) 0%, var(--kraft-mid) 55%, var(--kraft-dark) 100%);
    box-shadow: 2px 3px 6px rgba(0, 0, 0, 0.25);
  }
  .card--front { top: 90px; }
  .card--back { top: 470px; width: 558px; height: 342px; }

  .holder-name {
    position: absolute;
    top: 66px;
    left: 0;
    right: 0;
    margin: 0;
    text-align: center;
    font-size: 24px;
    font-weight: 700;
    letter-spacing: 0.5px;
  }
  .contact-icons {
    position: absolute;
    top: 113px;
    left: 187px;
    width: 180px;
    height: 24px;
  }
  .contact-lines {
    position: absolute;
    top: 148px;
    left: 0;
    right: 0;
    margin: 0;
    text-align: center;
    font-size: 16px;
    line-height: 20.5px;
  }
  .divider {
    position: absolute;
    top: 221px;
    left: 185px;
    width: 182px;
    height: 1px;
    background: var(--rule);
  }
  .company {
    position: absolute;
    top: 239px;
    left: 0;
    right: 0;
    margin: 0;
    text-align: center;
    font-size: 16px;
    line-height: 20px;
  }
  .company strong {
    display: block;
    font-weight: 700;
    letter-spacing: 0.3px;
  }
  .brand-name {
    position: absolute;
    top: 180px;
    left: 125px;
    margin: 0;
    font-size: 38px;
    font-weight: 400;
    color: var(--ink);
  }
</style>
</head>
<body>
<main class="canvas">
  <section class="card card--front">
    <h1 class="holder-name">MAYA TORVELL</h1>
    <svg class="contact-icons" viewBox="0 0 180 24" aria-hidden="true">
      <line x1="0" y1="12" x2="50" y2="12" stroke="#6b5539" stroke-width="1"/>
      <line x1="130" y1="12" x2="180" y2="12" stroke="#6b5539" stroke-width="1"/>
      <rect x="52" y="1" width="22" height="22" rx="3" fill="#1f1a15"/>
      <path d="M57 15 q6 -9 12 0 v3 h-12 z M59 9 h8 v3 h-8 z" fill="#c9a472"/>
      <rect x="79" y="1" width="22" height="22" rx="3" fill="#1f1a15"/>
      <rect x="83" y="7" width="14" height="10" fill="none" stroke="#c9a472" stroke-width="1.5"/>
      <path d="M83 7 l7 6 l7 -6" fill="none" stroke="#c9a472" stroke-width="1.5"/>
      <rect x="106" y="1" width="22" height="22" rx="3" fill="#1f1a15"/>
      <circle cx="117" cy="12" r="7" fill="none" stroke="#c9a472" stroke-width="1.5"/>
      <path d="M110 12 h14 M117 5 q-4 7 0 14 M117 5 q4 7 0 14" fill="none" stroke="#c9a472" stroke-width="1"/>
    </svg>
    <p class="contact-lines">
      <span class="phone">02 6481 7395</span><br>
      <span class="email">maya@kelvadtrading.com.au</span><br>
      <span class="website">www.heritagehollow.com.au</span>
    </p>
    <div class="divider"></div>
    <p class="company">
      <strong>HERITAGE HOLLOW</strong>
      <span class="address">PO Box Glenwarra NSW 2791</span>
    </p>
  </section>

  <section class="card card--back">
    <p class="brand-name">Heritage Hollow</p>
  </section>
</main>
</body>
</html>
```